Unique Builder wordpress website - Supply Graphics Only

We need a brand new website for a building company in Perth, Australia who constructs insulated panels (sip).
What is a SIP?
A SIP is a high-performance building panel used for floors, walls, and roofs in residential and commercial buildings. Panels are typically made using Expanded Polystyrene (EPS) sandwiched between two structural skins.
The design must incorporate a slick professional look and keep to the logo colours (Lime green & Blacks). The logo must not change colours or be altered. (
We will convert the graphics to a wordpress site. We have our own coders)
Design:
The website design must be clean, mobile friendly and the final design will be adapted to WordPress CMS.
The menus must contain dropdown menus and front page may contain a youtube video at a later date.
Fonts must be clear and easy to read
The contact us page will need to have an online form and google map.
The 16 pages listed will be the complete site and are for reference only. For this project the winning designer would need to supply the Homepage, and 1 inner pages only as PSD files.
The structure is as follows:
Home
About us
Marlow Fen Dwellings
What is a sip
Benefits
FAQ
Designs
Residential
Granny Flats
Architectural design
Photo Gallery <--- Would be great if a sample design can be provided
Services
Project management and custom design
Site Assembly
Kit Supply
Contact us
***We don't need the designer to design every page however a 1 inner page would be ideal****
Our Competitors websites
Note: the following websites look crap however, the following websites are some of our competitors. We want a clean and awesome layout.
http://www.corvamoda.com.au/
http://dralventorix.com.au/
http://www.quilbarrow.net.au/
New home builders and commercial builders
Building
5+ page

```html
<!DOCTYPE html>
<html lang="en">
<head>
<meta charset="utf-8">
<title>Tarnwell Panels – Home</title>
<link href="https://fonts.googleapis.com/css2?family=Raleway:wght@400;500;600&family=Open+Sans:wght@400;600&display=swap" rel="stylesheet">
<style>
:root{
  --lime:#9ac42e;
  --lime-dark:#7fa81f;
  --lime-light:#b3d54a;
  --yellow:#f3e61c;
  --ink:#222;
  --text:#555;
  --grey-bar:#dedede;
  --footer:#262626;
  --footer-base:#1c1c1c;
  --white:#fff;
}
*{margin:0;padding:0;box-sizing:border-box}
html,body{width:834px;height:1200px;overflow:hidden}
body{font-family:"Open Sans",sans-serif;color:var(--text);background:var(--white)}
.page{position:relative;width:834px;height:1200px;overflow:hidden;background:linear-gradient(180deg,#f7f7f7 0%,#fff 40%,#fafafa 60%)}
.abs{position:absolute}

.top-bar{left:0;top:0;width:834px;height:24px;background:var(--grey-bar)}
.top-links{position:absolute;right:124px;top:6px;font-size:8px;color:#555;font-family:"Raleway",sans-serif}
.top-links span{padding:0 4px;border-left:1px solid #888}
.top-links span:first-child{border-left:none}

.brand{left:126px;top:38px;display:flex;align-items:center;gap:8px}
.brand-mark{width:14px;height:14px;background:var(--lime);border-radius:50%}
.brand-name{font-family:"Raleway",sans-serif;font-weight:600;font-size:22px;color:var(--ink)}
.call{right:125px;top:55px;text-align:right;font-family:"Raleway",sans-serif}
.call-label{font-size:10.5px;color:var(--ink)}
.call-number{display:flex;align-items:center;gap:4px;font-size:15px;color:var(--ink);margin-top:1px}

.main-nav{left:126px;top:94px;width:583px;height:34px;background:linear-gradient(180deg,var(--lime-light),var(--lime));display:flex}
.main-nav a{flex:auto;display:flex;align-items:center;justify-content:center;font-size:8.6px;color:var(--white);text-decoration:none;font-family:"Raleway",sans-serif;font-weight:500;border-left:1px solid rgba(255,255,255,.35);padding:0 4px;white-space:nowrap}
.main-nav a:first-child{border-left:none;background:var(--lime-dark)}

.hero{left:126px;top:128px;width:583px;height:266px;background:linear-gradient(135deg,#8b8476 0%,#b59a62 45%,#d3b25e 70%,#7a6a4e 100%)}
.hero-caption{left:154px;top:212px;width:260px;height:104px;background:rgba(40,40,40,.82);padding:18px 22px}
.hero-kicker{font-family:"Raleway",sans-serif;color:var(--lime-light);font-size:14px;font-weight:500}
.hero-title{font-family:"Raleway",sans-serif;color:var(--white);font-size:18px;font-weight:500;margin-top:3px}
.hero-text{color:#ccc;font-size:7.6px;line-height:12.5px;margin-top:8px}
.hero-dots{left:386px;top:372px;display:flex;gap:3px}
.hero-dots i{width:12px;height:12px;border-radius:50%;background:rgba(255,255,255,.6)}
.hero-dots i:first-child{background:var(--white)}

.welcome{left:126px;top:418px;width:330px}
.welcome h1{font-family:"Raleway",sans-serif;font-weight:400;font-size:19px;color:var(--ink)}
.welcome p{font-size:7.4px;line-height:12.5px;margin-top:8px}
.welcome ul{list-style:none;margin-top:5px}
.welcome li{font-size:7.6px;line-height:17.6px;padding-left:11px;position:relative}
.welcome li::before{content:"";position:absolute;left:1px;top:6px;border-left:4px solid var(--lime);border-top:3px solid transparent;border-bottom:3px solid transparent}

.video{left:471px;top:423px;width:238px;height:143px;background:linear-gradient(160deg,#5b6e86,#9fa2a6 55%,#c8a27a)}
.video-play{position:absolute;left:104px;top:50px}
.video-bar{position:absolute;left:0;bottom:0;width:100%;height:22px;background:#222;display:flex;align-items:center;padding:0 6px;gap:6px}
.video-track{flex:1;height:4px;background:#ddd;border-radius:2px;position:relative}
.video-track::before{content:"";position:absolute;left:0;top:0;height:4px;width:40%;background:#3d8ed8;border-radius:2px}

.categories{left:0;top:603px;width:834px;height:201px;background:linear-gradient(180deg,#2e3338,#3b4048 50%,#23272b)}
.category{position:absolute;top:36px;width:150px;text-align:center;color:var(--white)}
.category-ring{width:60px;height:60px;margin:0 auto;border:2px solid var(--white);border-radius:50%;display:flex;align-items:center;justify-content:center}
.category h3{font-family:"Raleway",sans-serif;font-weight:400;font-size:14px;margin-top:6px}
.category p{font-size:6.8px;line-height:9px;color:#ddd;margin-top:2px}

.service{position:absolute;top:826px;width:186px;height:159px}
.service-photo{width:186px;height:90px}
.service-body{height:69px;padding:10px 16px;border-bottom-right-radius:14px}
.service-body h3{font-family:"Raleway",sans-serif;font-weight:400;font-size:13.5px;color:var(--white)}
.service-body p{font-size:6.6px;line-height:9px;margin-top:3px;color:var(--white)}
.service--lime .service-body{background:var(--lime-light)}
.service--yellow .service-body{background:var(--yellow)}
.service--yellow h3{color:var(--ink)}
.service--yellow p{color:#444}

.footer{left:0;top:1010px;width:834px;height:154px;background:var(--footer)}
.footer-col{position:absolute;top:30px;height:96px}
.footer-col + .footer-col{border-left:1px solid #444}
.footer-col h4{font-family:"Raleway",sans-serif;font-weight:400;font-size:12px;color:var(--white);margin-bottom:5px}
.footer-col a{display:block;font-size:8px;line-height:16px;color:#ddd;text-decoration:none}
.footer-col p{font-size:8px;color:#ddd}
.social{display:flex;gap:3px;margin-top:6px}
.social i{width:19px;height:19px;border:1.5px solid var(--yellow);border-radius:50%}
.footer-base{left:0;top:1164px;width:834px;height:36px;background:var(--footer-base)}
.footer-base p{position:absolute;left:127px;top:13px;font-size:6.6px;color:#ccc}
</style>
</head>
<body>
<div class="page">

  <div class="abs top-bar">
    <div class="top-links"><span>Photo Gallery</span><span>FAQ</span><span>Project management and custom design</span><span>Site Assembly</span><span>Kit Supply</span><span>Contact us</span></div>
  </div>

  <div class="abs brand">
    <span class="brand-mark"></span>
    <span class="brand-name">Tarnwell Panels</span>
  </div>

  <div class="abs call">
    <div class="call-label">Call Us Today!</div>
    <div class="call-number">
      <svg width="16" height="16" viewBox="0 0 16 16"><circle cx="8" cy="8" r="8" fill="#9ac42e"/><path d="M5.2 4.2l1.3-.3.8 1.9-.9.8c.5 1 1.2 1.7 2.1 2.1l.8-.9 1.9.8-.3 1.3c-3.2.2-5.9-2.5-5.7-5.7z" fill="#fff"/></svg>
      216.555.0147
    </div>
  </div>

  <nav class="abs main-nav">
    <a>Home</a><a>About us</a><a>Marlow Fen Dwellings</a><a>What is a sip</a><a>Benefits</a><a>FAQ</a><a>Designs</a><a>Residential</a><a>Granny Flats</a><a>Architectural design</a>
  </nav>

  <div class="abs hero" role="img" aria-label="Warm modern living room with concrete walls, timber floor, sofa and floor lamps"></div>
  <div class="abs hero-caption">
    <div class="hero-kicker">SPECIALISED IN</div>
    <div class="hero-title">RESIDENTIAL &amp; BUILDING</div>
    <div class="hero-text">Class aptent taciti sociosqu ad litora torquent<br>per conubia nostra per inceptos hymen</div>
  </div>
  <div class="abs hero-dots"><i></i><i></i><i></i><i></i></div>

  <section class="abs welcome">
    <h1>Welcome to Tarnwell Panels</h1>
    <p>Tarnwell Panels are designers and manufacturers of an engineered structural insulated panel and concealed structural frame building product. sips is rapidly becoming the building method of choice because of its overwhelming benefits and proven suitability</p>
    <ul>
      <li>High level of captive insulation. (warm in winter cool in summer)</li>
      <li>Very strong, light weight and durable.</li>
      <li>20 + year history of performance in cyclonic locations in WA</li>
      <li>Reduced build time (save time save money it's that easy)</li>
      <li>Energy efficient ( less energy to build and less energy to run ie lower power bills)</li>
    </ul>
  </section>

  <div class="abs video" role="img" aria-label="Video still of a city skyline with a curved overpass at dusk">
    <svg class="video-play" width="30" height="30" viewBox="0 0 30 30"><circle cx="15" cy="15" r="13.5" fill="none" stroke="#fff" stroke-width="2"/><path d="M12 9l9 6-9 6z" fill="#fff"/></svg>
    <div class="video-bar">
      <svg width="8" height="8" viewBox="0 0 8 8"><path d="M1 0l7 4-7 4z" fill="#fff"/></svg>
      <div class="video-track"></div>
      <svg width="10" height="8" viewBox="0 0 10 8"><path d="M0 2.5h2l3-2.5v8l-3-2.5h-2z" fill="#fff"/><path d="M7 2c1 1 1 3 0 4M8.5 1c1.6 1.6 1.6 4.4 0 6" stroke="#fff" fill="none"/></svg>
    </div>
  </div>

  <section class="abs categories" role="img" aria-label="Dusky view of modern commercial building facades">
    <div class="category" style="left:115px">
      <div class="category-ring"><svg width="30" height="28" viewBox="0 0 30 28"><rect x="2" y="3" width="26" height="22" fill="none" stroke="#f3e61c" stroke-width="2.5"/><rect x="7" y="8" width="9" height="12" fill="none" stroke="#f3e61c" stroke-width="2"/><path d="M19 8h5M19 13h5M19 18h5" stroke="#f3e61c" stroke-width="2"/></svg></div>
      <h3>Designs</h3>
      <p>ultrices Ut nisi erat fermentum vel<br>congue id euismod in elit Fusce<br>ultricies orci ac feugiat</p>
    </div>
    <div class="category" style="left:269px">
      <div class="category-ring"><svg width="30" height="28" viewBox="0 0 30 28"><path d="M3 14L15 3l12 11" fill="none" stroke="#f3e61c" stroke-width="2.5"/><path d="M7 12v13h16V12" fill="none" stroke="#f3e61c" stroke-width="2.5"/><rect x="12" y="16" width="6" height="9" fill="#f3e61c"/></svg></div>
      <h3>Residential</h3>
      <p>ultrices Ut nisi erat fermentum vel<br>congue id euismod in elit Fusce<br>ultricies orci ac feugiat</p>
    </div>
    <div class="category" style="left:420px">
      <div class="category-ring"><svg width="30" height="28" viewBox="0 0 30 28"><rect x="3" y="3" width="24" height="22" fill="#f3e61c"/><path d="M3 13h10M13 3v6M17 13h10M17 13v12M9 19h8" stroke="#2e3338" stroke-width="2"/></svg></div>
      <h3>Architectural</h3>
      <p>ultrices Ut nisi erat fermentum vel<br>congue id euismod in elit Fusce<br>ultricies orci ac feugiat</p>
    </div>
    <div class="category" style="left:570px">
      <div class="category-ring"><svg width="30" height="28" viewBox="0 0 30 28"><rect x="6" y="3" width="18" height="23" fill="none" stroke="#f3e61c" stroke-width="2.5"/><path d="M10 8h2M14 8h2M18 8h2M10 12h2M14 12h2M18 12h2M10 16h2M14 16h2M18 16h2M10 20h2M18 20h2" stroke="#f3e61c" stroke-width="2"/></svg></div>
      <h3>Granny Flats</h3>
      <p>ultrices Ut nisi erat fermentum vel<br>congue id euismod in elit Fusce<br>ultricies orci ac feugiat</p>
    </div>
  </section>

  <article class="service service--lime" style="left:126px">
    <div class="service-photo" role="img" aria-label="Bright open-plan lounge with sofa and round rug" style="background:linear-gradient(135deg,#c7b69a,#8a6c4f 60%,#d8d2c8)"></div>
    <div class="service-body"><h3>Marlow Fen Dwellings</h3><p>Donec dictum lectus non odio Cras a ante<br>vitae enim iaculis aliquam</p></div>
  </article>
  <article class="service service--yellow" style="left:324px">
    <div class="service-photo" role="img" aria-label="Modern kitchen with black pendant lights and timber cabinets" style="background:linear-gradient(135deg,#3a3d40,#9b8a73 55%,#e6e4e0)"></div>
    <div class="service-body"><h3>Our Services</h3><p>Donec dictum lectus non odio Cras a ante vitae enim<br>iaculis aliquam ultrices Ut nisi erat fermentum vel</p></div>
  </article>
  <article class="service service--lime" style="left:521px">
    <div class="service-photo" role="img" aria-label="White kitchen bench with cooktop and timber wall ovens" style="background:linear-gradient(135deg,#e8e6e2,#d0cbc4 50%,#8e5e3a)"></div>
    <div class="service-body"><h3>What is a Sip</h3><p>Donec dictum lectus non odio Cras a ante vitae enim<br>iaculis aliquam ultrices Ut nisi erat fermentum vel</p></div>
  </article>

  <footer class="abs footer">
    <div class="footer-col" style="left:127px;width:97px">
      <h4>Quick Links</h4><a>Home</a><a>About us</a><a>Marlow Fen Dwellings</a><a>What is a sip</a>
    </div>
    <div class="footer-col" style="left:224px;width:109px;padding-left:26px">
      <h4>Why Us</h4><a>Benefits</a><a>FAQ</a><a>Designs</a><a>Residential</a>
    </div>
    <div class="footer-col" style="left:333px;width:124px;padding-left:28px">
      <h4>Resources</h4><a>Granny Flats</a><a>Architectural design</a><a>Photo Gallery</a><a>Services</a>
    </div>
    <div class="footer-col" style="left:457px;width:133px;padding-left:17px;height:110px">
      <h4>Sublinks</h4><a>Project management and</a><a>custom design</a><a>Site Assembly</a><a>Kit Supply</a><a>Contact us</a>
    </div>
    <div class="footer-col" style="left:590px;width:140px;padding-left:16px;height:96px">
      <h4>Stay in Touch</h4><p>Please connect with Us on</p>
      <div class="social"><i></i><i></i><i></i><i></i></div>
    </div>
  </footer>
  <div class="abs footer-base"><p>© 2016 Company Name &nbsp;All right reserved &nbsp;Term of Use</p></div>

</div>
</body>
</html>
```